Quillmere Supply Chain and Logistic Consulting

Please review the attached Business Card. I want as close to this card with the colors, fonts, and quality of the card as possible. The attached compass should replace the deer head on both sides of the card and the text should say:

Backside
Compass JPEG
Quillmere SC&L
A Supply Chain and Logistics Consulting Company

Frontside
Quillmere SC&L
Ray Falkner - Tampa Florida
President
____________________________________
(555) 314-9027
QuillmereSCL@Examplemail.com
_____________________________________

Bottom Front Side

Target Market(s)

Businesses

Contact Information for Business Card

Backside
Compass JPEG
Quillmere SC&L

Frontside
Quillmere SC&L
President
(555) 314-9027
QuillmereSCL@Examplemail.com

Bottom Front Side

Font styles to use
Serif
Script

Colors

Designer to choose colors to be used in the design.

Requirements
Must have
• See attached card for reference
Nice to have
Should not have

```html
<!DOCTYPE html>
<html lang="en">
<head>
<meta charset="utf-8">
<title>Quillmere SC&amp;L Business Card</title>
<link rel="stylesheet" href="https://fonts.googleapis.com/css2?family=EB+Garamond:wght@400;500&display=swap">
<style>
  :root {
    --stage: #141414;
    --card: #1c1c1d;
    --card-edge: #0c0c0c;
    --ink: #f2f2f2;
    --ink-soft: #bdbdbd;
    --rule: #6a6a6a;
    --ghost: #242425;
    --mark: #d8d8d8;
  }
  * { margin: 0; padding: 0; box-sizing: border-box; }
  html, body { width: 1200px; height: 900px; overflow: hidden; background: var(--stage); }
  .stage { position: relative; width: 1200px; height: 900px; }

  .card {
    position: absolute;
    background: var(--card);
    box-shadow: 0 0 0 1px var(--card-edge), 0 18px 40px rgba(0,0,0,.6);
    overflow: hidden;
    font-family: 'EB Garamond', serif;
  }

  /* Front (portrait) */
  .card-front { left: 110px; top: 130px; width: 380px; height: 640px; padding: 46px 40px; }
  .brand-name {
    font-weight: 400; color: var(--ink);
    font-size: 30px; line-height: 1; letter-spacing: 0;
  }
  .brand-tagline {
    color: var(--ink-soft); font-size: 12px; margin-top: 8px; line-height: 1.2;
  }
  .divider { width: 70px; height: 1px; background: var(--rule); margin: 28px 0 24px; }
  .person-name {
    font-weight: 500; color: var(--ink);
    font-size: 24px; line-height: 1;
  }
  .person-role {
    color: var(--ink-soft); font-size: 15px; margin-top: 6px; line-height: 1.2;
  }
  .contact-list { list-style: none; margin-top: 22px; }
  .contact-item {
    display: flex; align-items: center; gap: 10px;
    color: var(--ink); font-size: 15px; line-height: 1.6;
  }
  .contact-icon { width: 12px; height: 12px; flex: none; }
  .ghost-shape { position: absolute; right: -70px; bottom: -60px; }

  /* Back (landscape) */
  .card-back {
    left: 560px; top: 130px; width: 560px; height: 340px;
    display: flex; align-items: center; justify-content: center;
  }
  .back-lockup { display: flex; flex-direction: column; align-items: center; }
  .back-dot { margin-bottom: 20px; }
  .back-name {
    font-weight: 400; color: var(--ink);
    font-size: 40px; line-height: 1;
  }
  .back-tagline {
    color: var(--ink-soft); font-size: 14px; margin-top: 10px; line-height: 1.2;
  }
</style>
</head>
<body>
<main class="stage">

  <section class="card card-front" aria-label="Card front">
    <h1 class="brand-name">Quillmere SC&amp;L</h1>
    <p class="brand-tagline">A Supply Chain &amp; Logistics Consulting Company</p>
    <div class="divider"></div>
    <h2 class="person-name">Ray Falkner</h2>
    <p class="person-role">President</p>
    <ul class="contact-list">
      <li class="contact-item">
        <svg class="contact-icon" viewBox="0 0 12 12" aria-hidden="true"><path d="M2.5 1l2 2.2-1 1.3c.7 1.5 1.6 2.4 3 3l1.3-1 2.2 2-1.3 1.8C4.9 10 2 7.1 1 2.3z" fill="#f2f2f2"/></svg>
        (555) 314-9027
      </li>
      <li class="contact-item">
        <svg class="contact-icon" viewBox="0 0 12 12" aria-hidden="true"><rect x="1" y="2.5" width="10" height="7" fill="#f2f2f2"/><path d="M1 2.5l5 4 5-4" fill="none" stroke="#1c1c1d" stroke-width="1"/></svg>
        QuillmereSCL@Examplemail.com
      </li>
      <li class="contact-item">
        <svg class="contact-icon" viewBox="0 0 12 12" aria-hidden="true"><circle cx="6" cy="6" r="5" fill="none" stroke="#f2f2f2" stroke-width="1.2"/><ellipse cx="6" cy="6" rx="2.2" ry="5" fill="none" stroke="#f2f2f2" stroke-width="1"/><path d="M1 6h10" stroke="#f2f2f2" stroke-width="1"/></svg>
        www.quillmerescl.com
      </li>
    </ul>
    <svg class="ghost-shape" width="320" height="320" viewBox="0 0 320 320" role="img" aria-label="Faint brand emblem area">
      <circle cx="160" cy="160" r="150" fill="var(--ghost)"/>
    </svg>
  </section>

  <section class="card card-back" aria-label="Card back">
    <div class="back-lockup">
      <svg class="back-dot" width="80" height="80" viewBox="0 0 80 80" aria-hidden="true">
        <circle cx="40" cy="40" r="39" fill="var(--mark)"/>
      </svg>
      <h2 class="back-name">Quillmere SC&amp;L</h2>
      <p class="back-tagline">A Supply Chain &amp; Logistics Consulting Company</p>
    </div>
  </section>

</main>
</body>
</html>
```